Business card for medical clinic

I need an upmarket, modern medical/health business card for my clinic

Contact Information for Business Card

name, address, email, qr code

```html
<!DOCTYPE html>
<html lang="en">
<head>
<meta charset="UTF-8">
<title>Corvell Health Partners – Business Card</title>
<link href="https://fonts.googleapis.com/css2?family=Montserrat:wght@400;500;700&display=swap" rel="stylesheet">
<style>
  :root {
    --stage: #2b2b2d;
    --sky: #29a9e1;
    --ocean: #13608f;
    --navy: #0f4a73;
    --ink: #1b1b1d;
    --paper: #ffffff;
    --brand-text: #1a6a9c;
  }
  * { margin: 0; padding: 0; box-sizing: border-box; }
  html, body {
    width: 1200px; height: 880px; overflow: hidden;
    background: var(--stage);
    font-family: "Montserrat", sans-serif;
  }
  .canvas { position: relative; width: 1200px; height: 880px; }

  .card {
    position: absolute; width: 520px; height: 300px;
    border-radius: 22px; overflow: hidden;
    box-shadow: 0 18px 40px rgba(0,0,0,.45);
  }

  /* front */
  .card-front {
    left: 50px; top: 150px;
    background: linear-gradient(160deg, var(--sky) 0%, #1f8fc7 45%, var(--ocean) 100%);
    display: flex; align-items: center; justify-content: center; gap: 18px;
  }
  .brand-dot {
    width: 44px; height: 44px; border-radius: 50%;
    background: var(--navy); flex: none;
  }
  .card-front .brand-name {
    color: var(--navy); font-weight: 700; font-size: 28px;
    letter-spacing: 1px; text-transform: uppercase; line-height: 1.15;
  }

  /* back */
  .card-back { left: 630px; top: 420px; background: var(--paper); }
  .card-back .wave { position: absolute; inset: 0; z-index: 0; }
  .card-back .brand {
    position: absolute; left: 200px; top: 44px; z-index: 1;
    display: flex; align-items: center; gap: 12px;
  }
  .card-back .brand-dot { width: 30px; height: 30px; background: var(--brand-text); }
  .card-back .brand-name {
    color: var(--brand-text); font-weight: 700; font-size: 18px;
    letter-spacing: .8px; text-transform: uppercase; line-height: 1.2;
  }
  .person { position: absolute; left: 34px; top: 188px; z-index: 1; }
  .person-name { color: var(--sky); font-weight: 700; font-size: 21px; letter-spacing: .5px; line-height: 24px; }
  .person-role { color: var(--paper); font-size: 12.5px; line-height: 16px; margin-top: 1px; }
  .contact-list {
    position: absolute; left: 34px; top: 238px; z-index: 1; list-style: none;
    color: var(--paper); font-size: 11.5px; line-height: 15px;
  }
  .contact-list li { display: flex; align-items: center; gap: 7px; }
  .contact-list svg { width: 11px; height: 11px; fill: var(--sky); flex: none; }
  .address {
    position: absolute; right: 26px; top: 200px; z-index: 1;
    color: var(--paper); font-size: 12.5px; text-align: right; line-height: 18px;
  }
</style>
</head>
<body>
<main class="canvas">

  <section class="card card-front" aria-label="Card front">
    <span class="brand-dot"></span>
    <span class="brand-name">Corvell Health<br>Partners</span>
  </section>

  <section class="card card-back" aria-label="Card back">
    <svg class="wave" viewBox="0 0 520 300" preserveAspectRatio="none" aria-hidden="true">
      <defs>
        <linearGradient id="stripe" x1="0" x2="1">
          <stop offset="0" stop-color="#0f4a73"/>
          <stop offset="1" stop-color="#29a9e1"/>
        </linearGradient>
      </defs>
      <path d="M40,168 C90,138 160,124 260,124 C420,124 495,104 514,26 L520,300 L40,300 Z" fill="#29a9e1"/>
      <path d="M25,176 C80,145 150,132 260,132 C420,132 497,112 517,32 L520,300 L25,300 Z" fill="#ffffff"/>
      <path d="M12,182 C65,152 145,138 260,138 C420,138 499,118 519,36 L520,300 L12,300 Z" fill="url(#stripe)"/>
      <path d="M0,190 C55,158 140,146 260,146 C420,146 500,126 520,42 L520,300 L0,300 Z" fill="var(--ink)"/>
    </svg>

    <div class="brand">
      <span class="brand-dot"></span>
      <span class="brand-name">Corvell Health<br>Partners</span>
    </div>

    <div class="person">
      <p class="person-name">DANIEL REYES</p>
      <p class="person-role">Managing Director</p>
    </div>

    <ul class="contact-list">
      <li><svg viewBox="0 0 24 24"><path d="M6.6 10.8a15 15 0 0 0 6.6 6.6l2.2-2.2a1 1 0 0 1 1-.25 11.4 11.4 0 0 0 3.6.57 1 1 0 0 1 1 1V20a1 1 0 0 1-1 1A17 17 0 0 1 3 4a1 1 0 0 1 1-1h3.5a1 1 0 0 1 1 1c0 1.250.2 2.45.57 3.57a1 1 0 0 1-.25 1z"/></svg>123 456 789</li>
      <li><svg viewBox="0 0 24 24"><path d="M2 5h20v14H2zm2 2v.5l8 5 8-5V7l-8 5z"/></svg>info@corvellhealth.com</li>
      <li><svg viewBox="0 0 24 24"><path d="M12 2a10 10 0 1 0 0 20 10 10 0 0 0 0-20zm0 2c.8 1.2 1.5 2.5 1.9 4h-3.8c.4-1.5 1.1-2.8 1.9-4zM4.3 14a8 8 0 0 1 0-4h3.4a16 16 0 0 0 0 4zm8 6c-.8-1.2-1.5-2.5-1.9-4h3.8c-.4 1.5-1.100 2.8-1.9 4zm2-6H9.7a14 14 0 0 1 0-4h4.6a14 14 0 0 1 0 4zm2 0a16 16 0 0 0 0-4h3.4a8 8 0 0 1 0 4z"/></svg>www.corvellhealth.com</li>
    </ul>

    <p class="address">Your address, City<br>State, Zip 1234</p>
  </section>

</main>
</body>
</html>
```